Vantor Apparel - T-Shirts on Storevia

Hi - I'm creating a new site to sell undershirts. The premise of the undershirt is that it has a U-neck shape so that your white undershirt does not show when you are wearing a button shirt. I want the site to be fun but still look stunning because I want to attract a certain clientele (business professionals with a sense of humor). I'm creating a funny video to post on the site to hopefully get some social media buzz.
I want the design to highlight the product but more importantly the lifestyle of the person who wears it. This is an undershirt so nobody really sees it and that's the point.
Since this is a single product that I want to sell, I want to make sure that the design works with Storevia. Since this is not for theme development, this design must work with an existing theme on Storevia (preferably free but if you must then no more than $75). You can choose the theme to design for.
Products:
* Single vantor undershirt in 4 sizes - S, M, L and XL
* 3 packs or 7 packs (buy 6 get 1 free)
* One-time purchase or subscription (delivery every 3 or 6 months) - I know this will require custom theme development
Attached you will find a very rough idea for the site and this was made before I had considered putting in a video (Brix template). It's going to be tough to catch lightning in a bottle much like Penny Razor Guild but that's what I'm hoping for.
Name of the company is Vantor Apparel. Logo attached. Included .ai file which has some funky colors so please use the light blue color logo similar to the png's attached.
Here is the site for a competitor. There's much to be improved on the site but I include it here because the concept of the undershirt is the same: http://www.mirelgarments.example
Feel free to use stock images that I can purchase on the site that represents a young and cool vibe. I will be taking shots of the shirts for the product page so for now use some generic shirt please.
Updates
Project Deadline Extended
Reason: Please take a look at feedback for other designs. I'm hoping for my mockup to be an inspiration, not just re-skinning the mockup I created. Plus it must be based on a Storevia theme. Use stock images as necessary but keep the budget for purchasing images under $100.
Target Market(s)
Male 30-50

```html
<!DOCTYPE html>
<html lang="en">
<head>
<meta charset="utf-8">
<title>Vantor Apparel — Undershirts for the Modern Man</title>
<link rel="stylesheet" href="https://fonts.googleapis.com/css2?family=Oswald:wght@500;700&family=Open+Sans:wght@400;600;700&display=swap">
<style>
:root{
  --blue:#2a9fd8;
  --blue-dark:#1c82bd;
  --blue-light:#4cb5e8;
  --ink:#1a1a1a;
  --charcoal:#2c2927;
  --charcoal-2:#3a3634;
  --grey-text:#8c8c8c;
  --light:#ececec;
  --white:#ffffff;
  --head:'Oswald', 'Arial Narrow', sans-serif;
  --body:'Open Sans', Arial, sans-serif;
}
*{box-sizing:border-box;margin:0;padding:0}
html,body{width:1200px;height:3214px;overflow:hidden}
body{position:relative;background:var(--white);font-family:var(--body);color:var(--ink)}
.abs{position:absolute}
a{color:inherit;text-decoration:none}

/* top bar */
.topbar{left:0;top:0;width:1200px;height:54px;background:#000;color:#fff;font-size:12px}
.topbar .welcome{left:94px;top:18px}
.topbar .utility{right:94px;top:18px;display:flex;gap:30px}
.topbar .utility span{display:flex;align-items:center;gap:7px}

/* header */
.header{left:0;top:54px;width:1200px;height:112px;background:#fff}
.brand{left:120px;top:34px;font-family:var(--body);font-weight:700;font-size:34px;color:var(--ink);letter-spacing:-.5px}
.nav{left:654px;top:46px;display:flex;gap:30px;font-family:var(--head);font-weight:500;font-size:14px;letter-spacing:.3px;align-items:center}

/* hero */
.hero{left:0;top:166px;width:1200px;height:442px;background:linear-gradient(90deg,#c4496f 0%,#d7a08a 28%,#8fd0f2 48%,#5fbcec 100%)}
.hero-tag{background:#fff;color:#000;font-family:var(--head);font-weight:700;font-size:26px;letter-spacing:1px;left:710px;top:287px;width:316px;height:53px;display:flex;align-items:center;justify-content:center}
.hero-title{background:#000;color:#fff;font-family:var(--head);font-weight:700;font-size:62px;left:656px;top:348px;width:429px;height:81px;display:flex;align-items:center;justify-content:center;letter-spacing:1px}
.hero-cta{background:#000;color:#fff;font-family:var(--head);font-weight:700;font-size:28px;left:769px;top:437px;width:257px;height:48px;display:flex;align-items:center;justify-content:center;letter-spacing:2px}

/* section titles */
.section-title{font-family:var(--head);font-weight:700;font-size:22px;letter-spacing:1px;display:flex;align-items:center;justify-content:center;border:2px solid var(--ink);height:54px}
.section-title.on-dark{border-color:#fff;color:#fff}

/* products */
.intro{left:160px;top:780px;width:880px;text-align:center;font-size:12.5px;line-height:20px;color:#666}
.read-more{font-family:var(--head);font-weight:700;font-size:11px;letter-spacing:.5px}
.product{width:320px;text-align:center}
.product-shot{width:270px;height:282px;margin:0 auto;background:radial-gradient(ellipse at center,#fdfdfd 0%,#e6e6e6 55%,#fff 78%)}
.product-name{margin-top:26px;font-family:var(--head);font-weight:700;font-size:14px;line-height:20px}
.price-row{width:209px;height:40px;margin:0 auto;display:flex;font-family:var(--head);font-weight:700;font-size:13px;color:#fff}
.price-row+.price-row{margin-top:10px}
.price-row .label{flex:1;background:var(--blue);display:flex;align-items:center;padding-left:14px}
.price-row .amount{width:74px;background:var(--blue-dark);display:flex;align-items:center;justify-content:center}
.price-rows{margin-top:24px}
.shop-now{left:482px;top:1420px;width:236px;height:53px}
.shop-now span{position:absolute;inset:0;display:flex;align-items:center;justify-content:center;color:#fff;font-family:var(--head);font-weight:700;font-size:22px;letter-spacing:1px}

/* blog */
.blog{left:0;top:1540px;width:1200px;height:750px;background:var(--charcoal)}
.post{width:298px;color:#fff}
.post-head{display:flex;align-items:center;gap:20px}
.post-num{width:43px;height:43px;background:var(--blue);display:flex;align-items:center;justify-content:center;font-family:var(--head);font-weight:700;font-size:24px}
.post-title{font-family:var(--head);font-weight:700;font-size:17px;position:relative}
.post-title::after{content:"";position:absolute;left:0;bottom:-8px;width:34px;height:2px;background:#fff}
.post p{margin-top:16px;font-size:12px;line-height:18px;color:#b5b5b5}
.post .read-more{display:block;margin-top:10px}

.promo{left:96px;top:2162px;width:1008px;height:123px;display:flex}
.promo-photo{width:410px;height:123px;background:linear-gradient(90deg,#8a8a8a,#5b5b5b);position:relative}
.promo-blue{flex:1;background:var(--blue);position:relative}
.promo-text{font-family:var(--head);font-weight:700;color:#fff;font-size:19px;line-height:24px}
.outline-btn{border:2px solid #fff;color:#fff;font-family:var(--head);font-weight:700;font-size:13px;display:flex;align-items:center;justify-content:center;letter-spacing:.5px}

/* testimonial + video */
.testimonial{left:96px;top:2472px;width:534px;height:220px;display:flex}
.testimonial-text{width:333px;background:var(--light);padding:40px 18px 0 18px}
.testimonial-text h3{font-family:var(--head);font-weight:700;font-size:17px;position:relative}
.testimonial-text h3::after{content:"";position:absolute;left:0;bottom:-9px;width:34px;height:2px;background:var(--ink)}
.testimonial-text p{margin-top:22px;font-size:12px;line-height:19px;color:#666}
.portrait{flex:1;background:linear-gradient(135deg,#e2e2e2,#b69a84 60%,#8d7465)}
.video{left:678px;top:2472px;width:345px;height:220px;background:linear-gradient(135deg,#b98a55,#7b6048 50%,#3f3a34)}

/* features */
.features{left:0;top:2759px;width:1200px;height:362px;background:var(--charcoal)}
.feature{width:334px;height:321px;background:var(--charcoal-2);color:#fff;text-align:center}
.feature-head{height:102px;background:var(--blue);display:flex;align-items:center;justify-content:center;gap:18px;font-family:var(--head);font-weight:700;font-size:19px}
.feature-head.alt{background:var(--blue-light)}
.feature .rule{width:40px;height:2px;background:#fff;margin:42px auto 0}
.feature p{margin:18px auto 0;width:270px;font-size:12px;line-height:19px;color:#b5b5b5}
.cards{display:flex;justify-content:center;gap:10px;margin-top:16px}
.cards span{width:54px;height:26px;background:#fff;color:#333;font-size:9px;font-weight:700;display:flex;align-items:center;justify-content:center}
.feature .outline-btn{width:134px;height:38px;margin:18px auto 0}

/* footer */
.footer{left:0;top:3121px;width:1200px;height:93px;background:#232120;color:#cfcfcf;font-size:11.5px}
.footer .copy{left:94px;top:38px}
.footer .links{left:416px;top:38px;display:flex;gap:24px}
.footer .social{right:96px;top:32px;display:flex;gap:10px}
.footer .social span{width:27px;height:27px}
</style>
</head>
<body>

<div class="topbar abs">
  <div class="welcome abs">Welcome to our online store! Login or Signup</div>
  <div class="utility abs">
    <span><svg width="11" height="11" viewBox="0 0 12 12"><circle cx="6" cy="6" r="4" fill="none" stroke="#fff" stroke-width="2"/></svg>Setting</span>
    <span><svg width="11" height="11" viewBox="0 0 12 12"><circle cx="6" cy="3.5" r="2.8" fill="#fff"/><path d="M1 12a5 5 0 0 1 10 0z" fill="#fff"/></svg>My Account</span>
    <span><svg width="13" height="11" viewBox="0 0 14 12"><path d="M0 1h3l2 7h7l2-5H4" fill="none" stroke="#fff" stroke-width="1.5"/><circle cx="6" cy="10.5" r="1.3" fill="#fff"/><circle cx="11" cy="10.5" r="1.3" fill="#fff"/></svg>Cart: 0 item</span>
  </div>
</div>

<header class="header abs">
  <div class="brand abs">Vantor Apparel</div>
  <nav class="nav abs">
    <a>HOME</a><a>CATEGORIES</a><a>ABOUT US</a><a>FAQs</a><a>CONTACT US</a>
    <svg width="14" height="14" viewBox="0 0 14 14"><circle cx="6" cy="6" r="4.5" fill="none" stroke="#1a1a1a" stroke-width="2"/><path d="M9.5 9.5 13 13" stroke="#1a1a1a" stroke-width="2"/></svg>
  </nav>
</header>

<section class="hero abs" role="img" aria-label="Smiling couple, man carrying woman piggyback under a bright blue sky"></section>
<div class="hero-tag abs">UNDERSHIRTS FOR THE</div>
<h1 class="hero-title abs">MODERN MAN</h1>
<a class="hero-cta abs">BUY NOW</a>

<h2 class="section-title abs" style="left:455px;top:678px;width:292px">OUR NEW PRODUCTS</h2>
<p class="intro abs">Lorem ipsum dolor sit amet rem eos illo omnis aut aperiam sit ipsam ipse odit aut aperiam aut aspernatur veritatis unde sed enim accusantium laudantium sunt perspiciatis ipsam sed doloremque ipsam dolores totam unde aut illo aut veritatis explicabo data quia dolores dicta sunt quasi eaque rem</p>
<a class="read-more abs" style="left:564px;top:850px">READ MORE</a>

<div class="product abs" style="left:121px;top:897px">
  <div class="product-shot" role="img" aria-label="Three pack of white undershirts"></div>
  <div class="product-name">VANTOR UNDERSHIRT<br>3 PACK OF SHIRTS</div>
  <div class="price-rows">
    <div class="price-row"><span class="label">BUY NOW</span><span class="amount">$15</span></div>
    <div class="price-row"><span class="label">EVERY 6 MONTH</span><span class="amount">$14</span></div>
  </div>
</div>
<div class="product abs" style="left:443px;top:897px">
  <div class="product-shot" role="img" aria-label="Seven pack of white undershirts"></div>
  <div class="product-name">VANTOR UNDERSHIRT<br>BUY 6 GET 1 FREE/7 SHIRTS</div>
  <div class="price-rows">
    <div class="price-row"><span class="label">BUY NOW</span><span class="amount">$78</span></div>
    <div class="price-row"><span class="label">EVERY 6 MONTH</span><span class="amount">$72</span></div>
  </div>
</div>
<div class="product abs" style="left:764px;top:897px">
  <div class="product-shot" role="img" aria-label="Three pack of white undershirts"></div>
  <div class="product-name">VANTOR UNDERSHIRT<br>3 PACK OF SHIRTS</div>
  <div class="price-rows">
    <div class="price-row"><span class="label">BUY NOW</span><span class="amount">$15</span></div>
    <div class="price-row"><span class="label">EVERY 6 MONTH</span><span class="amount">$14</span></div>
  </div>
</div>

<a class="shop-now abs">
  <svg width="236" height="53" viewBox="0 0 236 53"><polygon points="0,0 236,0 222,53 14,53" fill="#2a9fd8"/></svg>
  <span>SHOP NOW</span>
</a>

<section class="blog abs">
  <h2 class="section-title on-dark abs" style="left:429px;top:72px;width:340px">LATES NEWS FROM BLOG</h2>

  <article class="post abs" style="left:96px;top:190px"><div class="post-head"><span class="post-num">1</span><h3 class="post-title">AMET VOLUPTATEM</h3></div><p>Lorem ipsum dolor sit amet rem illo omnis aperiam sit ipsam ipsa odit aut aperiam aspernatur veritatis unde enim accusantium laudantium iudit sunt</p><a class="read-more">READ MORE</a></article>
  <article class="post abs" style="left:453px;top:190px"><div class="post-head"><span class="post-num">2</span><h3 class="post-title">AMET VOLUPTATEM</h3></div><p>Lorem ipsum dolor sit amet rem illo omnis aperiam sit ipsam ipsa odit aut aperiam aspernatur veritatis unde enim accusantium laudantium iudit sunt</p><a class="read-more">READ MORE</a></article>
  <article class="post abs" style="left:806px;top:190px"><div class="post-head"><span class="post-num">3</span><h3 class="post-title">AMET VOLUPTATEM</h3></div><p>Lorem ipsum dolor sit amet rem illo omnis aperiam sit ipsam ipsa odit aut aperiam aspernatur veritatis unde enim accusantium laudantium iudit sunt</p><a class="read-more">READ MORE</a></article>
  <article class="post abs" style="left:96px;top:399px"><div class="post-head"><span class="post-num">4</span><h3 class="post-title">AMET VOLUPTATEM</h3></div><p>Lorem ipsum dolor sit amet rem illo omnis aperiam sit ipsam ipsa odit aut aperiam aspernatur veritatis unde enim accusantium laudantium iudit sunt</p><a class="read-more">READ MORE</a></article>
  <article class="post abs" style="left:453px;top:399px"><div class="post-head"><span class="post-num">5</span><h3 class="post-title">AMET VOLUPTATEM</h3></div><p>Lorem ipsum dolor sit amet rem illo omnis aperiam sit ipsam ipsa odit aut aperiam aspernatur veritatis unde enim accusantium laudantium iudit sunt</p><a class="read-more">READ MORE</a></article>
  <article class="post abs" style="left:806px;top:399px"><div class="post-head"><span class="post-num">6</span><h3 class="post-title">AMET VOLUPTATEM</h3></div><p>Lorem ipsum dolor sit amet rem illo omnis aperiam sit ipsam ipsa odit aut aperiam aspernatur veritatis unde enim accusantium laudantium iudit sunt</p><a class="read-more">READ MORE</a></article>
</section>

<div class="promo abs">
  <div class="promo-photo" role="img" aria-label="Man wearing a white undershirt against a grey wall">
    <div class="promo-text abs" style="left:160px;top:38px">BUY 6 GET 1<br>FREE</div>
    <a class="outline-btn abs" style="left:287px;top:40px;width:100px;height:40px">SHOP NOW</a>
  </div>
  <div class="promo-blue">
    <div class="promo-text abs" style="left:28px;top:38px">ONE - TIME PURCHASE OR SUBSCRIPTION<br>DELIVERY EVERY 3 OR 6 MONTHS</div>
    <a class="outline-btn abs" style="left:460px;top:40px;width:100px;height:40px">SHOP NOW</a>
  </div>
</div>

<h2 class="section-title abs" style="left:238px;top:2357px;width:255px">WHAT THEY SAYS</h2>
<h2 class="section-title abs" style="left:710px;top:2357px;width:286px">HIGHLIGHTS PRODUCT</h2>

<div class="testimonial abs">
  <div class="testimonial-text">
    <h3>JOHN DOE, 25 YO</h3>
    <p>Lorem ipsum dolor sit amet rem illo quia aut aperiam sit ipsam ipsa odit aut aperiam aut aspernatur veritatis unde, sed enim accusan ipsam sed doloremque ...</p>
  </div>
  <div class="portrait" role="img" aria-label="Portrait of a customer"></div>
</div>
<div class="video abs" role="img" aria-label="Product video still of a young couple in a cafe">
  <svg class="abs" style="left:148px;top:86px" width="48" height="48" viewBox="0 0 48 48"><circle cx="24" cy="24" r="23" fill="#fff" opacity=".9"/><polygon points="19,14 35,24 19,34" fill="#6b5a4a"/></svg>
</div>

<section class="features abs">
  <div class="feature abs" style="left:96px;top:0">
    <div class="feature-head"><svg width="30" height="28" viewBox="0 0 30 28"><rect x="2" y="6" width="22" height="18" fill="none" stroke="#fff" stroke-width="2.5"/><path d="M8 6 22 1l2 5" fill="none" stroke="#fff" stroke-width="2.5"/><rect x="16" y="12" width="10" height="7" fill="#fff"/></svg>PAYMENT METHOD</div>
    <div class="rule"></div>
    <p>Lorem ipsum dolor sit amet, omnis aperiam</p>
    <div class="cards"><span>Cardix</span><span>Paynet</span><span>Walletly</span><span>Sendly</span></div>
    <a class="outline-btn" style="margin-top:34px;width:134px;height:38px;margin-left:auto;margin-right:auto">READ MORE</a>
  </div>
  <div class="feature abs" style="left:431px;top:0">
    <div class="feature-head alt"><svg width="36" height="24" viewBox="0 0 36 24"><rect x="0" y="2" width="22" height="15" fill="#fff"/><path d="M22 7h8l5 5v5H22z" fill="#fff"/><circle cx="7" cy="19" r="3.5" fill="#fff" stroke="#4cb5e8" stroke-width="1.5"/><circle cx="28" cy="19" r="3.5" fill="#fff" stroke="#4cb5e8" stroke-width="1.5"/></svg>FREE SHIPPING</div>
    <div class="rule"></div>
    <p>Lorem ipsum dolor sit amet, omnis aperiam sit ipsam ipsa odit aut aperiam aspernatur veritatis unde enim accusantium laudantium</p>
    <a class="outline-btn" style="margin-top:30px;width:134px;height:38px;margin-left:auto;margin-right:auto">READ MORE</a>
  </div>
  <div class="feature abs" style="left:769px;top:0">
    <div class="feature-head"><svg width="22" height="28" viewBox="0 0 22 28"><path d="M5 12V8a6 6 0 0 1 12 0v4" fill="none" stroke="#fff" stroke-width="3"/><rect x="1" y="12" width="20" height="15" fill="#fff"/></svg>SECURE SHOPPING</div>
    <div class="rule"></div>
    <p>Lorem ipsum dolor sit amet, omnis aperiam sit ipsam ipsa odit aut aperiam aspernatur veritatis unde enim accusantium laudantium</p>
    <a class="outline-btn" style="margin-top:30px;width:134px;height:38px;margin-left:auto;margin-right:auto">READ MORE</a>
  </div>
</section>

<footer class="footer abs">
  <div class="copy abs">© 2014 <b>YOUR COMPANY</b>. ALL RIGHTS RESERVED.</div>
  <div class="links abs"><a>ABOUT US</a><a>TERM AND USE</a><a>PRIVACY POLICY</a><a>FAQS</a><a>CONTACT US</a></div>
  <div class="social abs">
    <span style="background:#3b5998" aria-label="Social link one"></span>
    <span style="background:#2aa9e0" aria-label="Social link two"></span>
    <span style="background:#d23a2c" aria-label="Social link three"></span>
    <span style="background:#1f7bb6" aria-label="Social link four"></span>
    <span style="background:#c8232c" aria-label="Social link five"></span>
  </div>
</footer>

</body>
</html>
```